Wine label for family vineyard start-up

Brand new family vineyard needs a new label:

The information we need on the label is the following:
- Merlot & Cabernet (variety)
- Monte Braviasca (location)
- 2016 (vintage)

The style of the label should be graphic / minimal / masculine.

This is a wine made by three 35yr old guys

Target Market(s)

young & urban

Industry/Entity Type

Vineyard

Logo Text

Merlot & Cabernet / Monte Braviasca / 2016

Font styles to use
Sans Serif

Requirements
Must have
• clearly legible
• aesthetically pleasing [minimalist]
• sans serif

```html
<!DOCTYPE html>
<html lang="en">
<head>
<meta charset="utf-8">
<title>Merlot &amp; Cabernet 2016 – Wine Label</title>
<link rel="stylesheet" href="https://fonts.googleapis.com/css2?family=Patrick+Hand&display=swap">
<style>
  :root {
    --wine-centre: #7a1f24;
    --wine-edge: #571d23;
    --label-black: #1f1e1b;
    --label-ink: #ecebe6;
    --emblem-tone: #3b3935;
  }
  * { margin: 0; padding: 0; box-sizing: border-box; }
  html, body {
    width: 1200px;
    height: 1200px;
    overflow: hidden;
  }
  body {
    position: relative;
    background: radial-gradient(circle at 50% 50%, var(--wine-centre) 0%, var(--wine-edge) 75%);
    font-family: "Patrick Hand", sans-serif;
  }
  .wine-label {
    position: absolute;
    left: 400px;
    top: 282px;
    width: 373px;
    height: 638px;
    background: var(--label-black);
    color: var(--label-ink);
  }
  .emblem {
    position: absolute;
    left: 62px;
    top: 132px;
    width: 250px;
    height: 244px;
    border-radius: 50%;
    background: radial-gradient(circle, var(--label-black) 55%, var(--emblem-tone) 78%, var(--label-black) 92%);
  }
  .label-text {
    position: absolute;
    left: 0;
    width: 100%;
    text-align: center;
    white-space: nowrap;
    line-height: 1;
  }
  .variety {
    top: 484px;
    font-size: 37px;
    letter-spacing: 2px;
  }
  .location {
    top: 529px;
    font-size: 27px;
    letter-spacing: 5.5px;
    padding-left: 5.5px;
  }
  .vintage {
    top: 589px;
    font-size: 27px;
    letter-spacing: 5px;
    padding-left: 5px;
  }
</style>
</head>
<body>
  <main class="wine-label">
    <div class="emblem" role="img" aria-label="Hand-painted white brush-stroke ring emblem, open at the top"></div>
    <p class="label-text variety">Merlot &amp; Cabarnet</p>
    <p class="label-text location">MONTE BRAVIASCA</p>
    <p class="label-text vintage">2016</p>
  </main>
</body>
</html>
```